VENTURE CAPITAL GROUP BUSINESS CARD DESIGN

Venture Capital Group based in SF looking for a bold business card design. No trendy colour explosion, 3D effects etc. Just "simple" optical effects. Works on your brain, keeps your eye focused and sticks to your mind.
Target Market(s)
Technology startups
Industry/Entity Type
Venture Capital
Contact Information for Business Card
DESMOND WHITLAKE
MANAGING PARTNER
187 FENWORTH ST SAN FRANCISCO, CA 94187
415.555.0142 O
415.555.0147 F
415.555.0193 C
desmond@veldtmoorcapital.ventures

```html
<!DOCTYPE html>
<html lang="en">
<head>
<meta charset="utf-8">
<title>Veldtmoor Capital Group – Business Card</title>
<link href="https://fonts.googleapis.com/css2?family=Open+Sans:wght@400;600;700&display=swap" rel="stylesheet">
<style>
  :root {
    --backdrop: #2e3035;
    --card: #ffffff;
    --green: #1f8a3a;
    --green-soft: #9fd8a6;
    --green-mid: #6fb58f;
    --grey-light: #eeeeee;
    --grey-mid: #cfcfcf;
    --ink: #2a2a2a;
  }
  * { margin: 0; padding: 0; box-sizing: border-box; }
  html, body {
    width: 1200px; height: 864px; overflow: hidden;
    background: var(--backdrop);
    font-family: "Open Sans", Arial, sans-serif;
    color: var(--ink);
  }
  .card {
    position: absolute;
    left: 320px;
    width: 560px; height: 320px;
    background: var(--card);
    overflow: hidden;
  }
  .card--front { top: 72px; }
  .card--back { top: 472px; }

  /* Front */
  .front-mark {
    position: absolute; left: 50%; top: 62px;
    width: 96px; height: 96px; margin-left: -48px;
    border-radius: 50%;
    background: var(--grey-light);
  }
  .wordmark {
    color: var(--green);
    font-weight: 600;
    text-transform: uppercase;
    letter-spacing: 0.12em;
    line-height: 1.15;
  }
  .front-wordmark {
    position: absolute; left: 0; right: 0; top: 180px;
    text-align: center;
    font-size: 30px;
  }
  .front-wordmark small {
    display: block;
    font-size: 11px;
    letter-spacing: 0.42em;
    margin-top: 2px;
  }

  /* Back */
  .back-wordmark {
    position: absolute; left: 36px; top: 28px;
    font-size: 24px;
  }
  .back-wordmark small {
    display: block;
    font-size: 9px;
    letter-spacing: 0.4em;
    margin-top: 1px;
  }
  .contact {
    position: absolute; left: 36px; top: 96px;
    font-size: 12.5px; line-height: 1.45;
  }
  .contact-name {
    color: var(--green);
    font-weight: 700;
    font-size: 16px;
    line-height: 1.2;
  }
  .contact-title { font-size: 12.5px; margin-bottom: 14px; }
  .contact-address { margin-bottom: 12px; }
  .contact-list { list-style: none; }
  .contact-list li { display: flex; align-items: center; gap: 6px; }
  .contact-list svg { width: 11px; height: 11px; fill: var(--green); flex: none; }
  .decor-field {
    position: absolute; left: 300px; top: 40px;
    width: 290px; height: 300px;
    border-radius: 150px 0 0 0;
    background: linear-gradient(160deg, var(--green-soft) 0%, var(--green-mid) 35%, var(--grey-light) 70%, var(--grey-mid) 100%);
    opacity: 0.9;
  }
</style>
</head>
<body>

<section class="card card--front" aria-label="Card front">
  <div class="front-mark"></div>
  <div class="wordmark front-wordmark">Veldtmoor<small>Capital Group</small></div>
</section>

<section class="card card--back" aria-label="Card back">
  <div class="decor-field" role="img" aria-label="Large soft green and grey brand decoration"></div>
  <div class="wordmark back-wordmark">Veldtmoor<small>Capital Group</small></div>
  <div class="contact">
    <p class="contact-name">Desmond Whitlake</p>
    <p class="contact-title">Managing Partner</p>
    <p class="contact-address">187 Fenworth St San<br>Francisco, CA 94187</p>
    <ul class="contact-list">
      <li><svg viewBox="0 0 16 16" aria-hidden="true"><path d="M3 1l3 3-2 2c1 2 3 4 6 6l2-2 3 3-2 2C7 15 1 9 1 3z"/></svg>415.555.0142</li>
      <li><svg viewBox="0 0 16 16" aria-hidden="true"><path d="M4 1h7v4H4zM1 6h14v8H1zm3 2v2h8V8z"/></svg>415.555.0147</li>
      <li><svg viewBox="0 0 16 16" aria-hidden="true"><path d="M4 0h8v16H4zm1 2v10h6V2z"/></svg>415.555.0193</li>
      <li><svg viewBox="0 0 16 16" aria-hidden="true"><path d="M0 3h16v10H0zm1 1v1l7 4 7-4V4z"/></svg>desmond@veldtmoorcapital.ventures</li>
    </ul>
  </div>
</section>

</body>
</html>
```